Computer Company needs a Business card design

We need a business card design for our business. We assist people to transition to the KVS (Kestrel Vantage Scheme). The Verandal Crown Office-owned kvs™ network is a brand new telecommunications network currently being rolled out across Australia, giving access to a reliable broadband connection. Our niche market will predominantly be domestic customers in the 50+ age bracket. The assistance that we provide is everything from arranging the equipment, arranging the plan and contract term, appointment times, final testing of the network and any tweaks that need to be made. We basically PM the transition from start to finish. The business card design should be minimalist, should communicate loyalty and stability, should be easy to read and clearly explain what we do. We have asked for front and back. However, the back of the card does not have to include much information at all. It could be just a small design, or a repeat of our phone number. Up to you. The attached file only says what is required on the card. It does not specify where to arrange the text, what fonts to use, etc etc. As much as we would like to give you more info, due to our very limited design ability, we are not really able to send you any rough, or otherwise, designs of what we are after. Hopefully the above description is enough for you.

```html
<!DOCTYPE html>
<html lang="en">
<head>
<meta charset="utf-8">
<title>Linkstep Assist – Business Card</title>
<link rel="stylesheet" href="https://fonts.googleapis.com/css2?family=Questrial&display=swap">
<style>
  :root {
    --backdrop: #a8a8a8;
    --card-white: #f4f4f4;
    --brand-teal: #0786ad;
    --accent-orange: #ef7d11;
    --text-grey: #555555;
    --divider: #c8c8c8;
  }
  * { margin: 0; padding: 0; box-sizing: border-box; }
  html, body {
    width: 1200px;
    height: 960px;
    overflow: hidden;
    background: var(--backdrop);
    font-family: "Questrial", "Century Gothic", sans-serif;
  }
  .canvas {
    position: relative;
    width: 1200px;
    height: 960px;
  }
  .card {
    position: absolute;
    left: 320px;
    width: 602px;
    height: 344px;
    box-shadow: 0 3px 6px rgba(0,0,0,0.35);
  }
  .card-front {
    top: 98px;
    background: var(--card-white);
  }
  .card-back {
    top: 493px;
    background: var(--brand-teal);
    display: flex;
    align-items: center;
    justify-content: center;
  }
  .wordmark {
    position: absolute;
    left: 37px;
    top: 166px;
    font-size: 27px;
    line-height: 1;
    color: var(--brand-teal);
    -webkit-text-stroke: 0.7px var(--brand-teal);
    letter-spacing: 0.2px;
    white-space: nowrap;
  }
  .divider {
    position: absolute;
    left: 302px;
    top: 122px;
    width: 2px;
    height: 122px;
    background: var(--divider);
  }
  .contact-block {
    position: absolute;
    left: 325px;
    top: 124px;
  }
  .person-name {
    font-size: 21px;
    font-weight: 400;
    letter-spacing: 1px;
    color: var(--brand-teal);
    -webkit-text-stroke: 0.8px var(--brand-teal);
    line-height: 1.1;
  }
  .person-role {
    font-size: 16px;
    letter-spacing: 0.5px;
    color: var(--accent-orange);
    line-height: 1.2;
    margin-bottom: 10px;
  }
  .contact-list { list-style: none; }
  .contact-item {
    display: flex;
    align-items: center;
    gap: 8px;
    font-size: 14px;
    color: var(--text-grey);
    line-height: 19.5px;
  }
  .contact-icon { width: 13px; height: 13px; flex: none; }
  .back-wordmark {
    font-size: 50px;
    color: #ffffff;
    -webkit-text-stroke: 1.2px #ffffff;
    letter-spacing: 0.5px;
    white-space: nowrap;
    transform: translateY(-8px);
  }
</style>
</head>
<body>
<main class="canvas">
  <section class="card card-front" aria-label="Business card front">
    <div class="wordmark">Linkstep Assist</div>
    <div class="divider"></div>
    <div class="contact-block">
      <h1 class="person-name">ROWAN TELLISTER</h1>
      <p class="person-role">CEO/FOUNDER</p>
      <ul class="contact-list">
        <li class="contact-item">
          <svg class="contact-icon" viewBox="0 0 16 16" aria-hidden="true">
            <path fill="#0786ad" d="M3.6 1.2l2.2 2.6-1.3 1.8c.9 2.2 2.6 3.9 4.8 4.9l1.8-1.3 2.6 2.2-1.4 2.4C6.6 13.5 2.4 9.3 1.2 3.6z"/>
          </svg>
          0400555182
        </li>
        <li class="contact-item">
          <svg class="contact-icon" viewBox="0 0 16 16" aria-hidden="true">
            <rect x="1" y="3" width="14" height="10" fill="#0786ad"/>
            <path d="M1.5 3.5L8 9l6.5-5.5" fill="none" stroke="#f4f4f4" stroke-width="1.3"/>
          </svg>
          rowan@linkstepassist.com.au
        </li>
        <li class="contact-item">
          <svg class="contact-icon" viewBox="0 0 16 16" aria-hidden="true">
            <circle cx="8" cy="8" r="7" fill="#0786ad"/>
            <path d="M1.5 8h13M8 1c-2.6 2-2.6 12 0 14M8 1c2.6 2 2.6 12 0 14" fill="none" stroke="#f4f4f4" stroke-width="1"/>
          </svg>
          www.linkstepassist.com.au
        </li>
      </ul>
    </div>
  </section>

  <section class="card card-back" aria-label="Business card back">
    <div class="back-wordmark">Linkstep Assist</div>
  </section>
</main>
</body>
</html>
```